BUN AND BITE WALL POSTER

Hi designer,

I would like to create a poster to put on my wall.

My intention is to place a bicycle onto a wall and have these words vinyl stick next to it.

" Life is not a race.
It is a journey
Enjoy each moment. Relax!
Have a bowl of Bun and Bite
Make all your dreams come true "

I like traditional fonts - easy to read. See example. This is something I would love.

It will be on a white wall so black text would be ok. I have also attached my logo - maybe try include Bun and Bite font in your design if possible - but not important.

Good luck everyone.

Font styles to use
Decorative
Script

Requirements
Must have
• The placement of my bike will be on the top left corner of the wall so I think it will be best fit if all designs are done in horizontal rectangular shape (landscape)

```html
<!DOCTYPE html>
<html lang="en">
<head>
<meta charset="utf-8">
<title>Bun and Bite Wall Poster</title>
<link rel="stylesheet" href="https://fonts.googleapis.com/css2?family=Playball&display=swap">
<style>
  :root {
    --wall: #f6f6f6;
    --ink: #111111;
    --bike-dark: #3a3a3a;
    --bike-light: #d9d9d9;
  }
  html, body {
    margin: 0;
    padding: 0;
    overflow: hidden;
    background: var(--wall);
  }
  .poster {
    position: relative;
    width: 1200px;
    height: 1000px;
    background: var(--wall);
    overflow: hidden;
  }
  .bicycle-photo {
    position: absolute;
    left: 12px;
    top: 10px;
    width: 725px;
    height: 425px;
    border-radius: 40px;
    background: radial-gradient(ellipse at 50% 55%, var(--bike-dark) 0%, #8a8a8a 55%, var(--bike-light) 100%);
    opacity: 0.55;
    z-index: 0;
  }
  .quote {
    position: absolute;
    left: 340px;
    top: 450px;
    width: 715px;
    color: var(--ink);
    font-family: "Playball", cursive;
    text-align: center;
    z-index: 1;
  }
  .quote p {
    margin: 0;
    line-height: 1;
    white-space: nowrap;
  }
  .quote-lead {
    font-size: 64px;
    height: 80px;
    display: flex;
    align-items: center;
    justify-content: center;
  }
  .quote-sub {
    font-size: 44px;
    height: 60px;
    display: flex;
    align-items: center;
    justify-content: center;
    gap: 6px;
  }
  .quote-sub svg {
    width: 44px;
    height: 14px;
  }
  .quote-main {
    font-size: 60px;
    height: 65px;
    display: flex;
    align-items: center;
    justify-content: center;
  }
  .quote-divider {
    border: none;
    border-top: 2px dashed var(--ink);
    margin: 10px 0 18px;
  }
  .quote-brand {
    font-size: 58px;
    height: 68px;
    display: flex;
    align-items: center;
    justify-content: center;
  }
  .quote-close {
    font-size: 41px;
    height: 60px;
    display: flex;
    align-items: center;
    justify-content: center;
    gap: 8px;
  }
  .quote-close svg {
    width: 24px;
    height: 24px;
    fill: var(--ink);
  }
</style>
</head>
<body>
  <main class="poster">
    <div class="bicycle-photo" role="img" aria-label="Photograph of a black single-speed bicycle mounted on the wall"></div>

    <section class="quote">
      <p class="quote-lead">Life is not a race</p>
      <p class="quote-sub">
        <svg viewBox="0 0 44 14" aria-hidden="true"><path d="M2 10 C10 0, 18 14, 26 6 S38 4, 42 8" fill="none" stroke="#111" stroke-width="3" stroke-linecap="round"/></svg>
        <span>It is a journey</span>
        <svg viewBox="0 0 44 14" aria-hidden="true"><path d="M2 6 C8 2, 16 12, 24 6 S36 2, 42 8" fill="none" stroke="#111" stroke-width="3" stroke-linecap="round"/></svg>
      </p>
      <p class="quote-main">Enjoy each moment. Relax!</p>
      <hr class="quote-divider">
      <p class="quote-brand">Have a bowl of Bun and Bite</p>
      <p class="quote-close">
        <svg viewBox="0 0 24 24" aria-hidden="true"><path d="M12 1l3.2 7.2 7.8.7-5.9 5.2 1.8 7.7L12 17.8 5.1 21.8l1.8-7.7L1 8.9l7.8-.7z"/></svg>
        <span>Make all your dreams come true</span>
        <svg viewBox="0 0 24 24" aria-hidden="true"><path d="M12 1l3.2 7.2 7.8.7-5.9 5.2 1.8 7.7L12 17.8 5.1 21.8l1.8-7.7L1 8.9l7.8-.7z"/></svg>
      </p>
    </section>
  </main>
</body>
</html>
```